Field Trace Studies: Abductions

Book cover. Casebound and Perfect bound. Size 5.5 x 8.5 (portrait). Approx 165 pages for spine. Will be using Quillmark PressForge for printer so be sure to follow those specifications. This is a textbook for Search & Rescue and Law Enforcement search planners on deciding where they should look for someone who has been abducted. Nothing morbid. It will be a book in a series. The series is called Field Trace Studies. That should be in smaller letters at the top. Abductions should be the major title feature. The series will have a border on the front cover of safety orange (255, 121, 0) for RGB. vkM logo on front, spine, and back. Place holder for ISBN, author bio, book description, endorsements on back.

Target Market(s)

Professional textbook for Law Enforcement, Search and Rescue, Academic (criminologist)

Industry/Entity Type

Search and Rescue - Law Enforcement. Major colors for industry is orange for SAR and blue for Law enforcement

Requirements
Must have
• Safety Orange border (0.25 inch), vkM Logos, small Field Trace Studies title on top, large Abductions title. Author's name (Daniel P. Wrenfield)
Nice to have
• Not sure if picture or illustration works best. Topographic map is possible, law enforcement and searcher working together, clandestine grave, dirt road, all possible
Should not have
• no dead bodies, no bones, no skulls, no urban environment

```html
<!DOCTYPE html>
<html lang="en">
<head>
<meta charset="utf-8">
<title>Field Trace Studies: Abductions — Front Cover</title>
<link rel="stylesheet" href="https://fonts.googleapis.com/css2?family=Bebas+Neue&family=Source+Sans+3:wght@400&family=Open+Sans:wght@400&display=swap">
<style>
  :root {
    --safety-orange: #ff6008;
    --night-blue: #2e3862;
    --deep-navy: #08142f;
    --ridge-blue: #121d42;
    --paper: #ffffff;
    --text-light: #f4f5f8;
  }
  * { margin: 0; padding: 0; box-sizing: border-box; }
  html, body {
    width: 1200px;
    height: 934px;
    overflow: hidden;
    background: var(--paper);
  }
  .canvas {
    position: relative;
    width: 1200px;
    height: 934px;
  }
  .cover {
    position: absolute;
    left: 322px;
    top: 39px;
    width: 556px;
    height: 856px;
    background: var(--safety-orange);
  }
  .cover-field {
    position: absolute;
    left: 27px;
    top: 30px;
    right: 27px;
    bottom: 30px;
    background: var(--night-blue);
    overflow: hidden;
  }
  .ridge-art {
    position: absolute;
    left: 0;
    top: 0;
    width: 100%;
    height: 96px;
  }
  .search-scene-art {
    position: absolute;
    left: 0;
    bottom: 0;
    width: 100%;
    height: 420px;
    background: linear-gradient(180deg, rgba(8,20,47,0) 0%, rgba(18,29,66,0.65) 35%, var(--deep-navy) 72%, var(--deep-navy) 100%);
  }
  .title-block {
    position: absolute;
    left: 0;
    right: 0;
    top: 148px;
    text-align: center;
  }
  .series-line {
    display: flex;
    align-items: center;
    justify-content: center;
    gap: 12px;
    font-family: "Source Sans 3", "Source Sans Pro", sans-serif;
    font-size: 14.5px;
    color: var(--text-light);
    letter-spacing: 0.01em;
  }
  .series-rule {
    width: 76px;
    height: 1px;
    background: var(--text-light);
  }
  .book-title {
    margin-top: 4px;
    font-family: "Bebas Neue", "Oswald", sans-serif;
    font-weight: 400;
    font-size: 121px;
    line-height: 1;
    color: var(--safety-orange);
    letter-spacing: 0.005em;
  }
  .book-subtitle {
    margin-top: 6px;
    font-family: "Source Sans 3", "Source Sans Pro", sans-serif;
    font-size: 14px;
    line-height: 20px;
    color: var(--text-light);
  }
  .author-name {
    position: absolute;
    left: 0;
    right: 0;
    bottom: 52px;
    text-align: center;
    font-family: "Open Sans", sans-serif;
    font-size: 21px;
    letter-spacing: 0.2em;
    color: var(--text-light);
  }
</style>
</head>
<body>
  <main class="canvas">
    <section class="cover" aria-label="Front cover">
      <div class="cover-field">
        <svg class="ridge-art" viewBox="0 0 502 96" preserveAspectRatio="none" role="img" aria-label="Dark mountain ridge silhouette against the night sky">
          <path d="M0 0 H502 V26 C470 30 450 18 420 30 C390 40 360 30 330 38 C300 46 270 34 240 50 C210 62 180 52 150 62 C120 72 90 66 60 78 C40 86 20 90 0 94 Z" fill="var(--deep-navy)"/>
        </svg>
        <div class="search-scene-art" role="img" aria-label="Illustration: an officer with a flashlight and a searcher kneeling by disturbed ground in tall grass at night"></div>

        <header class="title-block">
          <p class="series-line"><span class="series-rule"></span>FIELD TRACE STUDIES<span class="series-rule"></span></p>
          <h1 class="book-title">ABDUCTIONS</h1>
          <p class="book-subtitle">SEARCH &amp; RESCUE AND LAW ENFORCEMENT<br>PLANNING GUIDE</p>
        </header>

        <p class="author-name">Daniel P. Wrenfield</p>
      </div>
    </section>
  </main>
</body>
</html>
```